LoopVane - A ride hailing server VAR

our Brindle.co profile: https://brindle.co/517loopvane

LOOPVANE offers first world solutions to first world problems. These days, our smartphones are our cameras, our wallets and our ride home. LOOPVANE guarantees that even if your phone is lost or dies, you'll never get stranded again. Simply call or text (SMS) our toll-free number to request a ride, and choose from one of the various services you subscribe to. LOOPVANE verifies your identity through a unique pin, making it possible to request rides through your own account from a stranger's phone via text or phone call. You can also login through our website or our App, making it easier than ever to get home phoneless.

LOOPVANE is a heterogeneous ride-hailing service that allows users for request transportation from any "transportation network company," taxi, helicopter service, jet service or any transportation service company that is publicly available. LOOPVANE will allow users to connect through our site, automated phone system, App or any appropriated touch point available.

Target Market(s)

RIde Haling

Coding

Coded - Design and coding required

Number of Pages Required

4 page

Requirements
Must have
• hav
Nice to have
• e the same functionality as our competitor's site: https://hopquill.com/
Should not have
• should not be cheezy
• We need to have the registration/sign up on the main page like https://www.zarvix.com/

```html
<!DOCTYPE html>
<html lang="en">
<head>
<meta charset="utf-8">
<title>LoopVane — Sign Up</title>
<link href="https://fonts.googleapis.com/css2?family=Open+Sans:wght@400;600;700&display=swap" rel="stylesheet">
<style>
  :root {
    --accent: #fbab0a;
    --nav-bg: #4a4a4a;
    --ink: #222222;
    --muted: #6b6b6b;
    --panel-bg: #f7f7f7;
    --panel-border: #dddddd;
    --field-border: #cfcfcf;
    --footer-bg: #121212;
    --footer-ink: #ffffff;
    --social-tile: #5d6a78;
    --btn-grey: #ececec;
  }
  * { box-sizing: border-box; margin: 0; padding: 0; }
  html, body { width: 1006px; height: 1200px; overflow: hidden; background: #fff; }
  body { position: relative; font-family: 'Open Sans', sans-serif; color: var(--ink); }
  .abs { position: absolute; }

  .brand { left: 74px; top: 18px; display: flex; align-items: center; gap: 7px; }
  .brand-mark { width: 49px; height: 49px; background: var(--accent); border-radius: 3px; }
  .brand-name { font-size: 20px; font-weight: 700; color: #2a2a2a; letter-spacing: 0.2px; }

  .service-car { top: 26px; width: 83px; height: 32px; background: var(--accent); border-radius: 14px 16px 8px 8px; }

  .main-nav { left: 0; top: 86px; width: 1006px; height: 48px; background: var(--nav-bg); }
  .nav-item { position: absolute; top: 0; height: 48px; line-height: 48px; transform: translateX(-50%);
    color: #fff; font-size: 11.5px; text-decoration: none; }
  .nav-item.is-active { color: var(--accent); }
  .nav-underline { left: 393px; top: 131px; width: 53px; height: 3px; background: var(--accent); }

  .section-title { left: 0; width: 1006px; text-align: center; font-size: 17.5px; font-weight: 400; color: var(--ink); }
  .social-tile { top: 230px; width: 60px; height: 60px; background: var(--social-tile); }

  .signup-panel { left: 278px; top: 362px; width: 450px; height: 526px; background: var(--panel-bg); border: 1px solid var(--panel-border); }
  .field-label { left: 311px; font-size: 13.5px; color: var(--ink); }
  .field-input { left: 311px; width: 383px; height: 42px; background: #fff; border: 1px solid var(--field-border);
    box-shadow: 0 1px 1px rgba(0,0,0,0.08); padding-left: 13px; font-family: inherit; font-size: 12px; color: var(--muted); line-height: 40px; }

  .btn { top: 802px; width: 116px; height: 37px; line-height: 37px; text-align: center; font-size: 14px; font-weight: 600; letter-spacing: 0.4px; }
  .btn-primary { left: 364px; background: var(--accent); color: #fff; }
  .btn-secondary { left: 526px; background: var(--btn-grey); color: #444; border: 1px solid #cfcfcf; }
  .btn-or { left: 493px; top: 809px; font-size: 15px; color: #333; }

  .site-footer { left: 0; top: 946px; width: 1006px; height: 254px; background: var(--footer-bg); }
  .footer-link { font-size: 11px; color: var(--footer-ink); display: flex; align-items: center; gap: 5px; }
  .footer-social { top: 1104px; width: 10px; height: 10px; border: 1.5px solid #fff; border-radius: 2px; }
  .store-badge { top: 990px; height: 25px; background: #000; border: 1px solid #8a8a8a; border-radius: 4px; }
  .footer-rule { left: 75px; top: 1144px; width: 857px; height: 1px; background: #555; }
  .copyright { left: 0; top: 1164px; width: 1006px; text-align: center; font-size: 11px; color: var(--footer-ink); }
</style>
</head>
<body>

<header>
  <div class="brand abs">
    <span class="brand-mark"></span>
    <span class="brand-name">LOOPVANE</span>
  </div>
  <div class="service-car abs" style="left:660px" role="img" aria-label="Yellow car illustration for a partner ride service"></div>
  <div class="service-car abs" style="left:752px" role="img" aria-label="Yellow car illustration for a second ride service"></div>
  <div class="service-car abs" style="left:843px" role="img" aria-label="Yellow car illustration for taxi service"></div>
</header>

<nav class="main-nav abs">
  <a class="nav-item" style="left:149px" href="#">HOME</a>
  <a class="nav-item" style="left:280px" href="#">ABOUT</a>
  <a class="nav-item is-active" style="left:417px" href="#">SIGN UP</a>
  <a class="nav-item" style="left:554px" href="#">SIGN IN</a>
  <a class="nav-item" style="left:694px" href="#">SUPPORT</a>
  <a class="nav-item" style="left:840px" href="#">CONTACT</a>
</nav>
<div class="nav-underline abs"></div>

<main>
  <h2 class="section-title abs" style="top:180px">SIGN IN USING YOUR RIDER OR SOCIAL ACCOUNTS</h2>
  <div class="social-tile abs" style="left:338px" role="img" aria-label="Social sign in option 1"></div>
  <div class="social-tile abs" style="left:427px" role="img" aria-label="Social sign in option 2"></div>
  <div class="social-tile abs" style="left:515px" role="img" aria-label="Social sign in option 3"></div>
  <div class="social-tile abs" style="left:604px" role="img" aria-label="Social sign in option 4"></div>
  <h2 class="section-title abs" style="top:310px">OR SIGN UP USING YOUR EMAIL</h2>

  <div class="signup-panel abs"></div>

  <label class="field-label abs" style="top:393px">First Name</label>
  <div class="field-input abs" style="top:418px">First Name</div>
  <label class="field-label abs" style="top:471px">Last Name</label>
  <div class="field-input abs" style="top:496px">Last Name</div>
  <label class="field-label abs" style="top:550px">Email</label>
  <div class="field-input abs" style="top:575px">Email</div>
  <label class="field-label abs" style="top:628px">Username</label>
  <div class="field-input abs" style="top:654px">Username</div>
  <label class="field-label abs" style="top:707px">Password</label>
  <div class="field-input abs" style="top:732px">Password</div>

  <div class="btn btn-primary abs">SIGN UP</div>
  <span class="btn-or abs">or</span>
  <div class="btn btn-secondary abs">SIGN IN</div>
</main>

<footer>
  <div class="site-footer abs"></div>

  <div class="footer-link abs" style="left:75px;top:978px">
    <svg width="8" height="10" viewBox="0 0 8 10"><path d="M4 0a4 4 0 0 0-4 4c0 3 4 6 4 6s4-3 4-6a4 4 0 0 0-4-4zm0 5.5A1.5 1.5 0 1 1 4 2.5a1.5 1.5 0 0 1 0 3z" fill="#fff"/></svg>
    Enter Your Location
  </div>
  <div class="footer-link abs" style="left:75px;top:1008px">
    <svg width="10" height="10" viewBox="0 0 10 10"><circle cx="5" cy="5" r="4.5" fill="#fff"/></svg>
    ENGLISH
  </div>
  <div class="footer-link abs" style="left:75px;top:1038px">
    <svg width="11" height="11" viewBox="0 0 11 11"><circle cx="5.5" cy="5.5" r="4.5" fill="none" stroke="#fff" stroke-width="1.6"/><circle cx="5.5" cy="5.5" r="1.8" fill="none" stroke="#fff" stroke-width="1.4"/></svg>
    Help
  </div>

  <span class="footer-social abs" style="left:76px"></span>
  <span class="footer-social abs" style="left:96px"></span>
  <span class="footer-social abs" style="left:117px"></span>
  <span class="footer-social abs" style="left:137px;border-radius:50%"></span>

  <a class="footer-link abs" style="left:340px;top:978px">Ride</a>
  <a class="footer-link abs" style="left:340px;top:1008px">Drive</a>
  <a class="footer-link abs" style="left:340px;top:1038px">Cities</a>
  <a class="footer-link abs" style="left:340px;top:1068px">Fare Estimate</a>
  <a class="footer-link abs" style="left:340px;top:1098px">How it Works</a>

  <a class="footer-link abs" style="left:586px;top:978px">Safety</a>
  <a class="footer-link abs" style="left:586px;top:1008px">Careers</a>
  <a class="footer-link abs" style="left:586px;top:1038px">Helping Cities</a>
  <a class="footer-link abs" style="left:586px;top:1068px">Our Story</a>
  <a class="footer-link abs" style="left:586px;top:1098px">Newsroom</a>

  <div class="store-badge abs" style="left:753px;width:86px" role="img" aria-label="App store download badge"></div>
  <div class="store-badge abs" style="left:850px;width:79px" role="img" aria-label="Mobile store download badge"></div>

  <div class="footer-rule abs"></div>
  <p class="copyright abs">Copyright © 2017. All Rights Reserved</p>
</footer>

</body>
</html>
```